Law Offices business card

Hi there, I'll need business card for the Law Offices of Colin Matheny. The information must convey his strategic approach and quick resolution to complex business litigation needs. Please emphasize Civil Litigation, Corporate Law, Business Governance and Real Estate Law. Colin has over 25 years of experience in these fields.The card should be modern and edgy and the message should be clear. Please consult his current website for ideas.

```html
<!DOCTYPE html>
<html lang="en">
<head>
<meta charset="utf-8">
<title>Law Offices of Colin Matheny – Business Card</title>
<link rel="stylesheet" href="https://fonts.googleapis.com/css2?family=Questrial&display=swap">
<style>
  :root {
    --ink: #231f20;
    --paper: #ffffff;
    --crimson: #a3161a;
    --crimson-dark: #6e0c0f;
    --text-dark: #231f20;
    --frame: #8a8a8a;
  }
  * { margin: 0; padding: 0; box-sizing: border-box; }
  html, body {
    width: 1200px; height: 343px; overflow: hidden;
    background: var(--paper);
    font-family: "Questrial", "Century Gothic", sans-serif;
  }
  .card-spread { position: relative; width: 1200px; height: 343px; }

  /* Front */
  .card-front {
    position: absolute; left: 0; top: 0; width: 601px; height: 343px;
    background: var(--paper); overflow: hidden;
  }
  .front-shapes { position: absolute; inset: 0; }
  .firm-mark {
    position: absolute; left: 36px; top: 124px; width: 200px;
    display: flex; align-items: flex-start; gap: 10px;
    color: var(--paper); font-size: 21px; line-height: 1.2;
  }
  .firm-mark .mark-square {
    flex: none; width: 14px; height: 14px; margin-top: 5px;
    background: var(--crimson);
  }
  .name-banner {
    position: absolute; left: 256px; top: 91px; width: 342px; height: 34px;
    background: var(--crimson); color: var(--paper);
    font-weight: 400; font-size: 27px; letter-spacing: 0.5px; line-height: 34px;
    text-align: center; text-transform: uppercase;
  }
  .job-title {
    position: absolute; left: 256px; top: 128px; width: 342px;
    text-align: center; font-size: 17px; color: var(--text-dark);
    text-transform: uppercase;
  }
  .contact {
    position: absolute; right: 41px; top: 216px;
    text-align: right; color: var(--text-dark); font-style: normal;
    font-size: 15.5px; line-height: 20px; text-transform: uppercase;
    white-space: nowrap;
  }
  .contact .address { margin-bottom: 6px; }
  .contact .phones { color: var(--crimson); margin-bottom: 5px; }

  /* Back */
  .card-back {
    position: absolute; left: 601px; top: 0; width: 599px; height: 343px;
    background: var(--ink);
  }
  .card-back .frame {
    position: absolute; left: 14px; top: 14px; right: 14px; bottom: 32px;
    border: 1px solid var(--frame);
  }
  .card-back .base-band {
    position: absolute; left: 0; right: 0; bottom: 0; height: 26px;
    background: var(--crimson);
  }
  .practice-areas {
    position: absolute; left: 0; right: 0; top: 68px;
    list-style: none; text-align: center; color: var(--paper);
    font-size: 30px; line-height: 39.5px; text-transform: uppercase;
  }
</style>
</head>
<body>
<main class="card-spread">
  <section class="card-front">
    <svg class="front-shapes" width="601" height="343" viewBox="0 0 601 343" aria-hidden="true">
      <defs>
        <linearGradient id="panelShade" x1="0" y1="0" x2="1" y2="1">
          <stop offset="0" stop-color="#2b2b2b"/>
          <stop offset="1" stop-color="#161616"/>
        </linearGradient>
      </defs>
      <polygon points="0,0 250,0 313,343 0,343" fill="url(#panelShade)"/>
      <polygon points="0,262 313,343 0,343" fill="#3b3b3d"/>
      <polygon points="248,91 256,91 256,137" fill="#6e0c0f"/>
    </svg>
    <div class="firm-mark">
      <span class="mark-square"></span>
      <span class="mark-name">Law Offices of Colin Matheny, PA</span>
    </div>
    <h1 class="name-banner">Colin Matheny</h1>
    <p class="job-title">Attorney</p>
    <address class="contact">
      <p class="address">118B Coral Avenue Palm Beach<br>Florida 33480</p>
      <p class="phones">561-555-0142 • 561-555-0187</p>
      <p class="email">colin@mathenylaw.com</p>
      <p class="web">www.mathenylaw.com</p>
    </address>
  </section>

  <section class="card-back">
    <div class="frame"></div>
    <ul class="practice-areas">
      <li>Civil Litigation</li>
      <li>Corporate Law</li>
      <li>Business Governance and</li>
      <li>Real Estate Law</li>
      <li>Title and Closing Services</li>
    </ul>
    <div class="base-band"></div>
  </section>
</main>
</body>
</html>
```